its a new company based in Christchurch new Zealand building computers ,repairs, upgrades and anything computers for the general public,i like bright happy colours like yellows, greens reds anything that stands out and it needs to communicant trust and security towards my new company,i have no logo yet,

Target Market(s)

target market of all ages

Industry/Entity Type

Building

Contact Information for Business Card

Byte Harbour Limited,ph-0218847261,email-tidelark77@mailvesta.test,14c marlowe cres,fenwick

```html
<!DOCTYPE html>
<html lang="en">
<head>
<meta charset="utf-8">
<title>Byte Harbour Limited – Business Cards</title>
<link rel="stylesheet" href="https://fonts.googleapis.com/css2?family=Exo+2:wght@500;600&family=Oswald:wght@500&family=Open+Sans:wght@400;600&display=swap">
<style>
  :root {
    --bg: #e9e6e1;
    --paper: #ffffff;
    --paper-shade: #f1f2f3;
    --sky: #0aa8dc;
    --sky-deep: #0995c4;
    --brand: #1a9fd3;
    --plum: #7b4a93;
    --leaf: #2aa84a;
    --ink-light: #ffffff;
    --map-tone: #e2e4e6;
  }
  * { margin: 0; padding: 0; box-sizing: border-box; }
  html, body {
    width: 1200px; height: 970px; overflow: hidden;
    background: var(--bg);
  }
  .sheet { position: relative; width: 1200px; height: 970px; }

  .card {
    position: absolute; left: 220px; width: 760px; height: 434px;
    background: var(--paper); overflow: hidden;
    box-shadow: 0 6px 18px rgba(0,0,0,.18);
  }
  .card--front { top: 34px; }
  .card--back  { top: 502px; }

  .band {
    position: absolute; left: 0; right: 0; bottom: 0; height: 200px;
    background: var(--sky);
  }
  .band__notch {
    position: absolute; top: -1px; width: 0; height: 0;
    border-left: 18px solid transparent; border-right: 18px solid transparent;
    border-top: 18px solid var(--paper);
  }
  .accent-line { position: absolute; height: 6px; }
  .accent-line--leaf { background: var(--leaf); left: 0; top: 228px; width: 170px; }
  .accent-line--plum { background: var(--plum); right: 0; top: 0; width: 380px; }

  .brand {
    position: absolute; display: flex; align-items: center; gap: 14px;
    font-family: "Exo 2", sans-serif; font-weight: 600;
    color: var(--brand); font-size: 38px; letter-spacing: .5px;
  }
  .brand__dot {
    width: 30px; height: 30px; border-radius: 50%; background: var(--plum);
    flex: none;
  }
  .card--front .brand { left: 70px; top: 120px; }
  .card--back .brand  { left: 60px; top: 130px; font-size: 34px; }

  .website {
    position: absolute; left: 0; right: 0; bottom: 70px; text-align: center;
    font-family: "Open Sans", sans-serif; font-size: 20px; letter-spacing: 6px;
    color: var(--ink-light);
  }

  .world-map {
    position: absolute; left: 230px; top: 10px; width: 440px; height: 210px;
    background: radial-gradient(ellipse at 50% 55%, var(--map-tone) 0%, rgba(226,228,230,.5) 55%, rgba(241,242,243,0) 75%);
  }

  .holder { position: absolute; left: 60px; bottom: 52px; color: var(--ink-light); }
  .holder__name {
    font-family: "Oswald", sans-serif; font-weight: 500; font-size: 46px;
    letter-spacing: 1px; line-height: 1;
  }
  .holder__role {
    font-family: "Open Sans", sans-serif; font-size: 14px; letter-spacing: 3px;
    margin-top: 8px;
  }

  .contacts {
    position: absolute; right: 40px; top: 248px; list-style: none;
    display: grid; grid-template-columns: auto auto; column-gap: 28px; row-gap: 18px;
    font-family: "Open Sans", sans-serif; font-size: 14px; color: var(--ink-light);
  }
  .contacts__item { display: flex; align-items: center; gap: 9px; white-space: nowrap; }
  .contacts__item--wide { grid-column: 1 / 3; }
  .contacts__icon {
    width: 24px; height: 24px; border-radius: 50%; border: 1.5px solid var(--ink-light);
    display: flex; align-items: center; justify-content: center; flex: none;
  }
  .contacts__icon svg { width: 13px; height: 13px; }
</style>
</head>
<body>
<main class="sheet">

  <section class="card card--front" aria-label="Business card front">
    <div class="accent-line accent-line--leaf"></div>
    <div class="brand"><span class="brand__dot"></span><span>Byte Harbour Limited</span></div>
    <div class="band">
      <span class="band__notch" style="left:190px"></span>
      <p class="website">www.byteharbour.test</p>
    </div>
  </section>

  <section class="card card--back" aria-label="Business card back">
    <div class="world-map" role="img" aria-label="Faint grey world map backdrop"></div>
    <div class="accent-line accent-line--plum"></div>
    <div class="brand"><span class="brand__dot"></span><span>Byte Harbour Limited</span></div>
    <div class="band">
      <span class="band__notch" style="left:170px"></span>
      <div class="holder">
        <p class="holder__name">RAVI TANE</p>
        <p class="holder__role">GENERAL MANAGER</p>
      </div>
      <ul class="contacts" style="top:48px">
        <li class="contacts__item">
          <span class="contacts__icon"><svg viewBox="0 0 16 16" fill="#fff"><path d="M3 1.5l3 .5 1 3-1.7 1.2a9 9 0 0 0 4.5 4.5L11 9l3 1 .5 3-2 1.5C7 14 2 9 1.5 3.5z"/></svg></span>
          021 884 7261
        </li>
        <li class="contacts__item">
          <span class="contacts__icon"><svg viewBox="0 0 16 16" fill="none" stroke="#fff" stroke-width="1.6"><rect x="1.5" y="3.5" width="13" height="9"/><path d="M1.5 3.5l6.5 5 6.5-5"/></svg></span>
          tidelark77@mailvesta.test
        </li>
        <li class="contacts__item">
          <span class="contacts__icon"><svg viewBox="0 0 16 16" fill="#fff"><path d="M3 1.5l3 .5 1 3-1.7 1.2a9 9 0 0 0 4.5 4.5L11 9l3 1 .5 3-2 1.5C7 14 2 9 1.5 3.5z"/></svg></span>
          021 884 7261
        </li>
        <li class="contacts__item">
          <span class="contacts__icon"><svg viewBox="0 0 16 16" fill="none" stroke="#fff" stroke-width="1.4"><circle cx="8" cy="8" r="6.5"/><ellipse cx="8" cy="8" rx="3" ry="6.5"/><path d="M1.5 8h13"/></svg></span>
          www.byteharbour.test
        </li>
        <li class="contacts__item contacts__item--wide">
          <span class="contacts__icon"><svg viewBox="0 0 16 16" fill="#fff"><path d="M8 1a5 5 0 0 0-5 5c0 4 5 9 5 9s5-5 5-9a5 5 0 0 0-5-5zm0 7a2 2 0 1 1 0-4 2 2 0 0 1 0 4z"/></svg></span>
          14c marlowe cres,fenwick
        </li>
      </ul>
    </div>
  </section>

</main>
</body>
</html>
```